Corporate Travel Technology Company needs new Business Card design

We need a new business card design to reflect our re-branded company. Our company is called tolvEn (pronounced tolvenn) and we provide Business Intelligence and mobile travel management solutions for the corporate travel industry. Our multinational customers use our solutions to manage large travel budgets and frequent travellers, as well as to save money and reduce risk. We'd like to see designs that use the blue and green palette as well as our corporate logo (attached below). The design should communicate innovation, insight, forward thinking, contemporary, trusted.

Target Market(s)

Large multinational corporates and Travel Agencies.

Industry/Entity Type

Business

Contact Information for Business Card

Rosalind Mercer
Chief Executive
tolvEn
Phone number - +61 (0)2 8134 2907
Email address - rosalind.mercer@tolven-example.com
Mobile number - +61 (0)438 516 702
www.tolven-example.com

Font styles to use
Other font styles liked:
• Please use font as close to corporate logo as possible

Colors
0255a3
0393ce
00a990
33b8a4
33a6d7
3176b5

Requirements
Must have
• Please include the words;
• Mobile Travel Management
• Accelerating Travel Business Insights
• Use corporate logo - although icon can be stylised if needed

```html
<!DOCTYPE html>
<html lang="en">
<head>
<meta charset="utf-8">
<title>tolvEn business card</title>
<link href="https://fonts.googleapis.com/css2?family=Open+Sans:wght@400;600&display=swap" rel="stylesheet">
<style>
  :root {
    --backdrop: #e4e5e6;
    --card-light: #eef2f8;
    --card-dark: #5b5d5c;
    --navy: #0255a3;
    --sky: #0393ce;
    --teal: #00a990;
    --teal-soft: #33b8a4;
    --ink: #1c1c1c;
    --white: #fbf8f8;
  }
  * { margin: 0; padding: 0; box-sizing: border-box; }
  html, body {
    width: 1189px; height: 1200px; overflow: hidden;
    background: var(--backdrop);
    font-family: "Open Sans", sans-serif;
  }
  .canvas { position: relative; width: 1189px; height: 1200px; }
  .card {
    position: absolute; left: 136px; width: 916px; height: 524px;
    box-shadow: 0 3px 10px rgba(0,0,0,0.18);
    overflow: hidden;
  }
  .card-front { top: 45px; background: var(--card-light); }
  .card-back { top: 600px; background: var(--card-dark); }

  .brand {
    position: absolute; left: 0; right: 0;
    display: flex; justify-content: center; align-items: center; gap: 22px;
  }
  .brand-dot { border-radius: 50%; flex: none; }
  .wordmark { font-weight: 600; letter-spacing: -1px; line-height: 1; }

  .card-front .brand { top: 128px; }
  .card-front .brand-dot { width: 44px; height: 44px; background: var(--sky); }
  .card-front .wordmark { font-size: 116px; color: var(--navy); }

  .card-back .brand { top: 222px; }
  .card-back .brand-dot { width: 52px; height: 52px; background: var(--teal-soft); }
  .card-back .wordmark { font-size: 136px; color: var(--white); }

  .taglines {
    position: absolute; left: 0; right: 0; top: 396px; text-align: center;
  }
  .tagline-main { font-size: 26px; font-weight: 600; color: var(--teal-soft); line-height: 1.4; }
  .tagline-sub { font-size: 22px; color: var(--white); line-height: 1.5; }

  .person { position: absolute; left: 78px; top: 330px; }
  .person-name { font-size: 37px; color: var(--sky); line-height: 1.1; }
  .person-title { font-size: 27px; color: var(--ink); line-height: 1.4; }

  .divider {
    position: absolute; left: 387px; top: 288px; width: 2px; height: 186px;
    background: var(--teal);
  }
  .contacts { position: absolute; left: 433px; top: 296px; list-style: none; }
  .contacts li {
    display: flex; align-items: center; height: 43px;
    font-size: 22px; color: var(--ink);
  }
  .contacts svg { width: 20px; height: 20px; margin-right: 24px; flex: none; }
</style>
</head>
<body>
<main class="canvas">
  <section class="card card-front" aria-label="Card front">
    <div class="brand">
      <span class="brand-dot"></span>
      <span class="wordmark">tolvEn</span>
    </div>

    <div class="person">
      <p class="person-name">Rosalind Mercer</p>
      <p class="person-title">Chief Executive</p>
    </div>

    <div class="divider"></div>

    <ul class="contacts">
      <li>
        <svg viewBox="0 0 20 20" aria-hidden="true"><rect width="20" height="20" fill="#0393ce"/><circle cx="10" cy="10" r="6" fill="none" stroke="#fff" stroke-width="1.6"/><path d="M4 10h12M10 4c-3 3-3 9 0 12M10 4c3 3 3 9 0 12" fill="none" stroke="#fff" stroke-width="1.2"/></svg>
        www.tolven-example.com
      </li>
      <li>
        <svg viewBox="0 0 20 20" aria-hidden="true"><rect width="20" height="20" fill="#0393ce"/><path d="M7 4l2 3-1.5 1.5c.8 1.8 2.2 3.2 4 4L13 11l3 2-1.5 2.5C10 15 5 10 4.5 5.5z" fill="#fff"/></svg>
        +61 (0)2 8134 2907
      </li>
      <li>
        <svg viewBox="0 0 20 20" aria-hidden="true"><rect width="20" height="20" fill="#0393ce"/><rect x="6.5" y="3" width="7" height="14" rx="1" fill="none" stroke="#fff" stroke-width="1.5"/><rect x="8" y="5" width="4" height="6" fill="#fff"/></svg>
        +61 (0)438 516 702
      </li>
      <li>
        <svg viewBox="0 0 20 20" aria-hidden="true"><rect width="20" height="20" fill="#0393ce"/><rect x="3.5" y="5.5" width="13" height="9" fill="none" stroke="#fff" stroke-width="1.5"/><path d="M3.5 5.5l6.5 5 6.5-5" fill="none" stroke="#fff" stroke-width="1.5"/></svg>
        rosalind.mercer@tolven-example.com
      </li>
    </ul>
  </section>

  <section class="card card-back" aria-label="Card back">
    <div class="brand">
      <span class="brand-dot"></span>
      <span class="wordmark">tolvEn</span>
    </div>
    <div class="taglines">
      <p class="tagline-main">Mobile Travel Management</p>
      <p class="tagline-sub">Accelerating Travel Business Insights</p>
    </div>
  </section>
</main>
</body>
</html>
```